Need a clean & modern homepage for an education site + opportunity for longer term work

Thanks for viewing our project. We are excited about this new website and we hope that we might build a relationship with designers as we work on this project. I provided quite a few details and requirements to help you more quickly create a design that meets our needs.
Who we are:
We are a website that discusses the importance of college accreditation and provides a directory of college programs.
What we need:
A homepage that meets the below requirements and is inspired by the examples provided
Definition of accredited:
ac·cred·it·ed [uh-kred-i-tid] adj.
1. officially recognized as meeting the essential requirements, as of academic excellence: accredited schools.
2. provided with official credentials, as by a government: an accredited diplomatic representative.
3. accepted as authoritative: an accredited theory.
Overall look and feel for the homepage:
- Clean, simple and modern
- Limited (or zero) pictures
- Utilize color blocks with text
- A trend seems to be longer vertical length homepages with lots of whitespace. I generally like this trend as long as the page is not way to tall.
Inspirations: Sites that have a similar look and feel to what I need.
http://lernvoxa.org/
http://www.campusmetrik.com/colleges/brantmoor-university/
http://quietfolding.org/
http://www.velostrahiring.com/
http://www.zunq.com/
http://sketches.bxv.com/
Items to be included on the homepage. Details below on each item.
- Top navigation
- Logo: Please leave a blank area for a logo. The logo has not been designed.
- Simple graphic/color block at the top that highlights a definition of “Accredited” – the definition should be formatted like it is being copy/pasted from a dictionary.
- Space for a video and small (50 word) written description of the video. You can use placeholder text.
- One section with 3 Paragraphs of content (each paragraph around 100 words) with a header at the top. You can use placeholder text but please create the formatting. At the end of the 3 paragraphs please have a “Read More” Note this shouldn't be 3 separate paragraphs with three read mores - it is 3 paragraphs with one read more at the end.
- An area with the header “Search Colleges by State” that has anchor text links to all 50 states.
Top navigation:
- Home
- States – with a subnav dropdown that includes all 50 US states.
- Programs – with a subnav dropdown that includes program titles (list below)
- Degrees - with a subnav dropdown that includes 5 degree levels (list below)
- Accreditation – no subnav
- Rankings – no subnav
- Resources – no subnav
Footer
- Link to about us, privacy, and a copyright www.url.com
Programs List for sub navigation
Accounting
Art
Bible
Business
Criminal Justice
Design
Education
Engineering
English
Law
LPN to RN
Management
Math
MBA
MPH
Medical Assisting
Military
Nursing
Occupational Therapy
Paralegal
Psychology
Pharmacy
RN to BSN
Radiology
Social Work
Sonography
Degrees list for sub navigation
Certificate
Associate
Bachelors
Masters
PhD
Thanks so much - looking forward to working with you!
Education

```html
<!DOCTYPE html>
<html lang="en">
<head>
<meta charset="utf-8">
<title>Accredited College Directory — Home</title>
<link href="https://fonts.googleapis.com/css2?family=Didact+Gothic&family=Montserrat:wght@600;700&display=swap" rel="stylesheet">
<style>
  :root {
    --navy: #1d2f5e;
    --nav-grey: #8a8f96;
    --sky: #3ab0e3;
    --cyan-band: #2fb8dd;
    --cyan-deep: #21a8d2;
    --ocean: #1882c4;
    --footer: #0f5f95;
    --green: #4cbf5d;
    --paper: #ebedef;
    --card: #ffffff;
    --text: #555a60;
    --white: #ffffff;
  }
  * { margin: 0; padding: 0; box-sizing: border-box; }
  html, body { width: 799px; height: 1200px; overflow: hidden; }
  body {
    position: relative;
    font-family: "Didact Gothic", "Century Gothic", sans-serif;
    color: var(--text);
    background: var(--paper);
    background-image: repeating-linear-gradient(45deg, rgba(255,255,255,.35) 0 1px, transparent 1px 4px);
  }
  .abs { position: absolute; }

  /* Header */
  .top-strip { left: 0; top: 0; width: 799px; height: 5px; background: var(--sky); }
  .site-header { left: 0; top: 5px; width: 799px; height: 54px; background: var(--white); }
  .site-name { left: 86px; top: 20px; font-family: "Montserrat", sans-serif; font-weight: 700; font-size: 14px; color: var(--navy); }
  .main-nav a { position: absolute; top: 23px; font-size: 12px; color: var(--nav-grey); text-decoration: none; }

  /* Hero */
  .hero { left: 0; top: 59px; width: 799px; height: 262px;
    background: linear-gradient(180deg, #8ee07a 0%, #6cd38c 30%, #7cd3e0 65%, #c9eef8 100%); }
  .definition { left: 183px; top: 91px; width: 439px; height: 96px; border: 2px solid rgba(255,255,255,.85); }
  .definition-text { left: 208px; top: 100px; width: 400px; font-family: "Montserrat", sans-serif; font-weight: 700;
    font-size: 12px; line-height: 18px; color: var(--white); text-transform: uppercase; letter-spacing: .4px; }
  .search-field { top: 230px; height: 24px; background: var(--white); border-radius: 3px; font-size: 11px; color: #888; padding: 6px 14px; }
  .search-button { left: 563px; top: 230px; width: 75px; height: 24px; background: var(--sky); color: var(--white);
    font-family: "Montserrat", sans-serif; font-weight: 600; font-size: 11px; text-align: center; line-height: 24px; }

  /* Video */
  .video-block { left: 140px; top: 285px; width: 518px; height: 123px; background: var(--green); box-shadow: 0 3px 4px rgba(0,0,0,.15); }
  .video-copy { left: 17px; top: 20px; width: 300px; font-size: 11.5px; line-height: 12px; color: var(--white); }
  .watch-btn { left: 142px; top: 80px; width: 111px; height: 24px; border: 1px solid var(--white); color: var(--white);
    font-size: 13px; text-align: center; line-height: 22px; }
  .video-frame { left: 346px; top: 12px; width: 154px; height: 100px; background: linear-gradient(135deg, #d9eef7, #8fc3dd); }

  /* Cards */
  .card { top: 437px; width: 204px; height: 205px; background: var(--card); }
  .card-icon { left: 8px; top: 14px; }
  .card h2 { position: absolute; left: 66px; top: 24px; width: 130px; font-family: "Montserrat", sans-serif; font-weight: 600;
    font-size: 13px; line-height: 15px; color: #5a5f66; }
  .card p { position: absolute; left: 10px; top: 72px; width: 186px; height: 92px; overflow: hidden; font-size: 9.3px; line-height: 10.3px; text-align: justify; }
  .read-more { position: absolute; left: 0; top: 166px; width: 204px; height: 26px; background: var(--sky); color: var(--white);
    font-size: 13px; text-align: center; line-height: 26px; }
  .read-more.is-active { background: var(--green); }

  /* News */
  .news-band { left: 0; top: 669px; width: 799px; height: 285px; background: linear-gradient(180deg, var(--cyan-band), var(--cyan-deep)); }
  .news-title { left: 0; top: 696px; width: 799px; text-align: center; font-family: "Montserrat", sans-serif; font-weight: 700; font-size: 28px; color: var(--white); }
  .news-item { top: 803px; width: 200px; }
  .news-date { position: absolute; left: 0; top: 0; width: 35px; height: 31px; background: #c9ccd0; color: var(--white);
    font-family: "Montserrat", sans-serif; font-weight: 700; font-size: 10.5px; line-height: 12px; text-align: center; padding-top: 4px; }
  .news-head { position: absolute; left: 35px; top: 0; width: 105px; height: 31px; background: var(--white); color: #666;
    font-size: 13px; line-height: 31px; padding-left: 8px; }
  .news-item p { position: absolute; left: 0; top: 42px; width: 198px; font-size: 9.3px; line-height: 11.3px; color: var(--white); }
  .news-more { position: absolute; left: 0; top: 110px; width: 94px; height: 19px; border: 1px solid var(--white); color: var(--white);
    font-size: 12px; line-height: 17px; padding-left: 10px; }

  /* Link directory */
  .links-band { left: 0; top: 954px; width: 799px; height: 190px; background: var(--ocean); }
  .logo-box { left: 74px; top: 977px; width: 147px; height: 138px; border: 2px solid var(--white); color: var(--white);
    font-family: "Montserrat", sans-serif; font-weight: 700; font-size: 22px; line-height: 22px; text-align: center; padding-top: 44px; }
  .col-title { font-family: "Montserrat", sans-serif; font-weight: 700; font-size: 16px; color: var(--white); }
  .link-list { list-style: none; font-size: 11px; line-height: 12.2px; color: var(--white); }
  .col-rule { top: 1005px; width: 1px; height: 112px; background: rgba(255,255,255,.6); }

  /* Footer */
  .site-footer { left: 0; top: 1144px; width: 799px; height: 56px; background: var(--footer); color: var(--white); font-size: 17px; }
  .site-footer span { position: absolute; top: 17px; }
</style>
</head>
<body>
  <div class="abs top-strip"></div>
  <header class="abs site-header">
    <div class="abs site-name">MY WEBSITE NAME</div>
    <nav class="main-nav">
      <a style="left:294px">Home</a><a style="left:343px">States</a><a style="left:392px">Programs</a>
      <a style="left:455px">Degrees</a><a style="left:519px">Accreditation</a><a style="left:598px">Rankings</a>
      <a style="left:661px">Resources</a>
    </nav>
  </header>

  <section class="abs hero" role="img" aria-label="Illustration of raised hands against a green and blue paint-splashed backdrop"></section>
  <div class="abs definition"></div>
  <p class="abs definition-text">Simple graphic/color block at the top that highlights a definition of “accredited” – the definition should be formatted like it is being copy/pasted from a dictionary.</p>
  <div class="abs search-field" style="left:154px;width:265px">Search Collage</div>
  <div class="abs search-field" style="left:428px;width:126px">State
    <svg class="abs" style="right:10px;top:6px" width="8" height="11" viewBox="0 0 8 11"><path d="M4 0a4 4 0 0 1 4 4c0 3-4 7-4 7S0 7 0 4a4 4 0 0 1 4-4z" fill="#bbb"/><circle cx="4" cy="4" r="1.5" fill="#fff"/></svg>
  </div>
  <div class="abs search-button">SEARCH</div>

  <section class="abs video-block">
    <p class="abs video-copy">written description of the videowritten description of the videowritten description of the video written description of the video written description of the video written description of the video written description of the video</p>
    <div class="abs watch-btn">Watch video</div>
    <svg class="abs" style="left:262px;top:82px" width="66" height="26" viewBox="0 0 66 26"><path d="M2 8 C10 26 40 26 60 10" stroke="#fff" stroke-width="1.6" fill="none"/><path d="M50 8 L62 8 L58 18" stroke="#fff" stroke-width="1.6" fill="none"/></svg>
    <div class="abs video-frame" role="img" aria-label="Video still of a smiling presenter">
      <svg class="abs" style="left:58px;top:31px" width="38" height="38" viewBox="0 0 38 38"><circle cx="19" cy="19" r="18" fill="#2f9fe0"/><path d="M15 11 L28 19 L15 27z" fill="#fff"/></svg>
    </div>
  </section>

  <article class="abs card" style="left:80px">
    <svg class="abs card-icon" width="52" height="52" viewBox="0 0 52 52"><circle cx="26" cy="26" r="24" fill="none" stroke="#444" stroke-width="2.5"/><path d="M12 22 L26 15 L40 22 L26 29z" fill="#444"/><path d="M18 26 v7 c4 4 12 4 16 0 v-7" fill="#444"/></svg>
    <h2>header at the top header at the top</h2>
    <p>One section with 3 Paragraphs of content (each paragraph around 100 words) with a header at the top. You can use placeholder text but please create the formatting. At the end of the 3 paragraphs please have a “Read More” Note this shouldn't be 3 separate paragraphs with three read mores - it is 3 paragraphs with one read more at the end.One section with 3 Paragraphs of content (each</p>
    <div class="read-more is-active">Read More</div>
  </article>
  <article class="abs card" style="left:297px">
    <svg class="abs card-icon" width="52" height="52" viewBox="0 0 52 52"><circle cx="26" cy="26" r="24" fill="none" stroke="#444" stroke-width="2.5"/><circle cx="26" cy="24" r="10" fill="none" stroke="#444" stroke-width="2.5"/><path d="M16 24 h20 M26 14 v20 M18 36 h16" stroke="#444" stroke-width="2"/></svg>
    <h2>header at the top header at the top</h2>
    <p>One section with 3 Paragraphs of content (each paragraph around 100 words) with a header at the top. You can use placeholder text but please create the formatting. At the end of the 3 paragraphs please have a “Read More” Note this shouldn't be 3 separate paragraphs with three read mores - it is 3 paragraphs with one read more at the end.One section with 3 Paragraphs of content (each</p>
    <div class="read-more">Read More</div>
  </article>
  <article class="abs card" style="left:518px">
    <svg class="abs card-icon" width="52" height="52" viewBox="0 0 52 52"><circle cx="26" cy="26" r="24" fill="none" stroke="#444" stroke-width="2.5"/><rect x="14" y="15" width="24" height="6" rx="2" fill="#444"/><rect x="16" y="23" width="22" height="6" rx="2" fill="#444"/><rect x="14" y="31" width="24" height="6" rx="2" fill="#444"/></svg>
    <h2>header at the top header at the top</h2>
    <p>One section with 3 Paragraphs of content (each paragraph around 100 words) with a header at the top. You can use placeholder text but please create the formatting. At the end of the 3 paragraphs please have a “Read More” Note this shouldn't be 3 separate paragraphs with three read mores - it is 3 paragraphs with one read more at the end.One section with 3 Paragraphs of content (each</p>
    <div class="read-more">Read More</div>
  </article>

  <section class="abs news-band"></section>
  <svg class="abs" style="left:340px;top:664px" width="120" height="30" viewBox="0 0 120 30"><path d="M0 5 L40 5 Q50 5 55 15 L60 24 L65 15 Q70 5 80 5 L120 5" fill="#ebedef"/><path d="M55 9 h10 M60 4 v10" stroke="#888" stroke-width="2.5"/></svg>
  <h1 class="abs news-title">Latest News</h1>
  <svg class="abs" style="left:0;top:750px" width="799" height="50" viewBox="0 0 799 50"><path d="M127 40 V8 H669 V40 M400 0 V40" stroke="#fff" stroke-width="1.3" fill="none"/><circle cx="127" cy="41" r="6" fill="#fff"/><circle cx="400" cy="41" r="6" fill="#fff"/><circle cx="669" cy="41" r="6" fill="#fff"/></svg>

  <article class="abs news-item" style="left:70px">
    <div class="news-date">30-6<br>2012</div><div class="news-head">News header</div>
    <p>One section with 3 Paragraphs of content (each paragraph around 100 words) with a header at the top. You can use placeholder text but please create the formatting. At the end of the 3 paragraphs please have a “Read More” Note this</p>
    <div class="news-more">Read More</div>
  </article>
  <article class="abs news-item" style="left:317px">
    <div class="news-date">30-6<br>2012</div><div class="news-head">News header</div>
    <p>One section with 3 Paragraphs of content (each paragraph around 100 words) with a header at the top. You can use placeholder text but please create the formatting. At the end of the 3 paragraphs please have a “Read More” Note this</p>
    <div class="news-more">Read More</div>
  </article>
  <article class="abs news-item" style="left:595px">
    <div class="news-date">30-6<br>2012</div><div class="news-head">News header</div>
    <p>One section with 3 Paragraphs of content (each paragraph around 100 words) with a header at the top. You can use placeholder text but please create the formatting. At the end of the 3 paragraphs please have a “Read More” Note this</p>
    <div class="news-more">Read More</div>
  </article>

  <section class="abs links-band"></section>
  <svg class="abs" style="left:374px;top:954px" width="52" height="16" viewBox="0 0 52 16"><path d="M0 0 H52 L26 16z" fill="#23a9d2"/><path d="M18 3 H34 L26 12z" fill="#fff"/></svg>
  <div class="abs logo-box">Your logo<br>here</div>
  <h3 class="abs col-title" style="left:237px;top:973px">Programs</h3>
  <ul class="abs link-list" style="left:241px;top:1003px"><li>Accounting</li><li>Art</li><li>Bible</li><li>Business</li><li>Criminal Justice</li><li>Design</li><li>Education</li><li>Engineering</li><li>English</li></ul>
  <div class="abs col-rule" style="left:351px"></div>
  <ul class="abs link-list" style="left:375px;top:1006px"><li>Accounting</li><li>Art</li><li>Bible</li><li>Business</li><li>Criminal Justice</li><li>Design</li><li>Education</li><li>Engineering</li><li>English</li></ul>
  <div class="abs col-rule" style="left:471px"></div>
  <ul class="abs link-list" style="left:492px;top:1011px"><li>Accounting</li><li>Art</li><li>Bible</li><li>Business</li><li>Criminal Justice</li><li>Design</li><li>Education</li><li>Engineering</li><li>English</li></ul>
  <div class="abs col-rule" style="left:589px"></div>
  <h3 class="abs col-title" style="left:607px;top:976px">Degrees</h3>
  <ul class="abs link-list" style="left:611px;top:1009px"><li>Accounting</li><li>Art</li><li>Bible</li><li>Business</li><li>Criminal Justice</li><li>Design</li><li>Education</li><li>Engineering</li><li>English</li></ul>

  <footer class="abs site-footer">
    <span style="left:70px">copyright@www.url.com</span>
    <span style="left:530px">about us</span>
    <span style="left:620px">privacy</span>
  </footer>
</body>
</html>
```